Harvest Gateway Fellowship Ministries needs a fresh new web design

We are an up and coming multicultural church that aims to bring people into a life changing encounter with God. We need a fresh and inviting website in order to increase our internet presence and make us easier to connect with.
Here are some of the basic requirements for the site:
• Clearly displayed address, service times, and contact info
• A staff profile page
• An area for a calendar with upcoming events and their details
• Social media buttons
• Group pages for the different ministries (youth, children’s church, men, etc…)
• An area for donations and eCommerce
• A resources page for assorted media (podcasts, sermons, videos, etc.…)
• An area for prayer requests.

```html
<!DOCTYPE html>
<html lang="en">
<head>
<meta charset="utf-8">
<title>Harvest Gateway Fellowship Ministries</title>
<link href="https://fonts.googleapis.com/css2?family=Open+Sans:wght@400;600;700&display=swap" rel="stylesheet">
<style>
:root{
  --accent:#d3401b;
  --green:#4b7d22;
  --gold:#f6b40f;
  --nav-red:#b7111b;
  --ink:#333;
  --muted:#6b6b6b;
  --dark:#2b2b2b;
  --slate:#3f4346;
  --event:#8a8a8a;
  --band:#f4f4f4;
  --band2:#ebebeb;
}
*{box-sizing:border-box;margin:0;padding:0}
html,body{width:870px;height:1200px;overflow:hidden}
body{font-family:"Open Sans",Arial,sans-serif;color:var(--ink);background:#fff;position:relative}
.abs{position:absolute}

/* header */
.site-header{left:0;top:0;width:870px;height:117px;background:linear-gradient(180deg,#fbdcc2,#fdf0e3)}
.brand{left:60px;top:36px;display:flex;align-items:center;gap:8px}
.brand-dot{width:32px;height:32px;border-radius:50%;background:var(--gold)}
.brand-name{font-size:12px;font-weight:700;color:var(--accent);line-height:1.3;width:140px}
.social{left:590px;top:20px;display:flex;gap:8px}
.social span{width:26px;height:26px;border-radius:50%;background:#5b86b8;border:2px solid #fff;box-shadow:0 1px 2px rgba(0,0,0,.3)}
.social span:nth-child(2){background:#5fb6e4}
.social span:nth-child(3){background:#c9302c}
.social span:nth-child(4){background:#ec8a25}
.social span:nth-child(5){background:#2f6ea7}
.cart{left:773px;top:21px;width:26px;height:26px;background:#3a3a3a;border-radius:2px;display:flex;align-items:center;justify-content:center}
.main-nav{left:310px;top:77px;display:flex;font-size:11.5px}
.main-nav a{color:var(--ink);text-decoration:none;padding:4px 7px;margin-right:19px;line-height:14px}
.main-nav a.active{background:var(--nav-red);color:#fff;border-radius:2px}

/* hero */
.hero{left:0;top:117px;width:870px;height:366px;
  background:
    radial-gradient(ellipse 55px 75px at 545px 175px,rgba(255,196,120,.95),rgba(255,160,90,0) 100%),
    radial-gradient(ellipse 135px 200px at 555px 190px,#c8703f 0%,#8e4a2e 40%,rgba(60,40,40,0) 78%),
    radial-gradient(ellipse 400px 260px at 200px 120px,#33415a 0%,rgba(40,50,70,0) 80%),
    linear-gradient(180deg,#222b3c,#2c3649 55%,#141925)}
.hero-quote{left:74px;top:256px;font-size:23.5px;font-weight:600;color:#fff;line-height:29px;text-shadow:0 1px 3px rgba(0,0,0,.5)}
.hero-btn{left:76px;top:323px;width:149px;height:28px;background:var(--gold);border-radius:2px;color:#3b2a00;font-size:12.5px;font-weight:600;text-align:center;line-height:28px}
.dots{left:398px;top:449px;width:74px;height:18px;background:rgba(0,0,0,.55);border-radius:9px;display:flex;gap:7px;justify-content:center;align-items:center}
.dots i{width:7px;height:7px;border-radius:50%;background:#fff}
.dots i:first-child{background:transparent;border:1.5px solid #fff}

/* welcome */
h2{font-weight:400;color:var(--accent);font-size:18px}
.welcome-title{left:73px;top:511px}
.welcome-text{left:74px;top:540px;width:532px;font-size:10px;line-height:16.6px;color:var(--muted)}
.welcome-text p+p{margin-top:6px}
.rule{left:72px;top:666px;width:537px;height:1px;background:#ddd}

.staff-title{left:73px;top:686px}
.donate-title{left:353px;top:686px}
.card{top:715px;width:124px;height:133px}
.card .photo{width:124px;height:100px}
.card .label{height:33px;line-height:33px;text-align:center;font-size:11px}
.staff .photo{background:radial-gradient(ellipse 22px 26px at 62px 38px,#5a3a2a 0%,#5a3a2a 80%,rgba(90,58,42,0) 100%),linear-gradient(180deg,#eef0f2 0%,#e2e5e8 55%,#2b2c30 62%,#1e1f23 100%)}
.staff .label{background:#3a3a3a;color:#eee}
.product .label{background:var(--gold);color:#3b2a00;font-size:12.5px;font-weight:600}
.product.gift .photo{background:linear-gradient(90deg,#b7a48f 0%,#efe7df 30%,#d8b9a0 50%,#f4efea 70%,#8f7f73 100%)}
.product.books .photo{background:linear-gradient(150deg,#f3e6cc 0%,#d8b284 45%,#9a6638 75%,#6b3c1c 100%)}

.groups{left:74px;top:871px;width:535px;height:102px;background:
  linear-gradient(90deg,#050505 0%,#080808 26%,rgba(8,8,8,0) 40%),
  linear-gradient(180deg,rgba(40,40,45,.2),rgba(30,30,35,.55)),
  repeating-linear-gradient(90deg,#b8653f 0 14px,#d9d4cf 14px 26px,#4c4f58 26px 40px,#c88c6a 40px 52px,#6e5548 52px 66px)}
.groups h3{position:absolute;left:13px;top:10px;font-size:14px;font-weight:600;color:var(--gold)}
.groups ul{position:absolute;left:14px;top:36px;list-style:none;color:#fff;font-size:10.5px;line-height:13.6px}
.groups li::before{content:"•";margin-right:6px}
.groups li.more{font-size:9px}

/* sidebar */
.video{left:624px;top:517px;width:174px;height:113px;background:radial-gradient(ellipse 50px 45px at 140px 45px,#a27a5e,rgba(120,90,70,0) 100%),linear-gradient(135deg,#8a8886,#4b4745 50%,#2f2a27)}
.play{left:698px;top:560px;width:26px;height:26px;border-radius:50%;background:#fff;border:2px solid #555;display:flex;align-items:center;justify-content:center}
.events-title{left:627px;top:648px;color:var(--green);font-size:14.5px;font-weight:400}
.cal{left:624px;top:676px;width:174px}
.cal-head{height:29px;background:var(--slate);color:#fff;font-size:11.5px;display:flex;justify-content:space-between;align-items:center;padding:0 9px}
.cal-head b{font-weight:400;font-size:8px}
.cal-days,.cal-grid{display:grid;grid-template-columns:repeat(7,1fr);gap:2px;padding:0 1px}
.cal-days{height:16px;font-size:6.5px;color:#555;text-align:center;line-height:16px;background:#f3f3f3}
.cal-grid{background:#fff;padding-top:1px}
.cal-grid span{height:23px;line-height:23px;text-align:center;font-size:10px;background:#e8e8e8;color:#333}
.cal-grid span.off{color:#bbb;background:#efefef}
.cal-grid span.today{background:#8b8f92;color:#fff}
.event{left:624px;width:174px;height:62px;background:var(--event);color:#fff;padding:9px 16px}
.event h4{font-size:11.5px;font-weight:600}
.event p{font-size:7.5px;line-height:12px;color:#eee;margin-top:3px}

/* verse */
.verse{left:0;top:1007px;width:870px;height:80px;background:var(--band);text-align:center}
.verse h3{font-size:14px;color:var(--green);font-weight:400;margin-top:19px}
.verse p{font-size:12px;color:var(--muted);margin-top:7px}
.verse p span{color:var(--ink)}

.contact{left:0;top:1087px;width:870px;height:61px;background:var(--band2);font-size:9.6px;color:var(--muted);line-height:16.5px}
.contact .item{position:absolute;top:14px;display:flex;align-items:center;gap:10px}

.site-footer{left:0;top:1148px;width:870px;height:52px;background:var(--dark);color:#9a9a9a;font-size:10px}
.site-footer .copy{position:absolute;left:74px;top:19px}
.cards{position:absolute;left:667px;top:19px;display:flex;gap:5px}
.cards span{width:22px;height:14px;border-radius:2px;background:#ddd}
</style>
</head>
<body>

<header class="abs site-header">
  <div class="abs brand"><span class="brand-dot"></span><span class="brand-name">Harvest Gateway Fellowship Ministries</span></div>
  <div class="abs social" aria-label="Social media"><span></span><span></span><span></span><span></span><span></span></div>
  <div class="abs cart" aria-label="Shop">
    <svg width="14" height="12" viewBox="0 0 14 12"><path d="M1 4h12l-1.5 7h-9z" fill="#fff"/><path d="M4 4l3-3 3 3" stroke="#fff" fill="none"/></svg>
  </div>
  <nav class="abs main-nav">
    <a class="active">HOME</a><a>ABOUT US</a><a>EVENTS</a><a>PRAYER REQUEST</a><a>DONATE</a><a>CONTACT US</a>
  </nav>
</header>

<section class="abs hero" role="img" aria-label="Open cupped hands glowing with warm light over dark foliage"></section>
<div class="abs hero-quote">"No limits, No Boundaries,<br>but increase in Jesus name"</div>
<div class="abs hero-btn">REQUEST FOR PRAYER</div>
<div class="abs dots"><i></i><i></i><i></i><i></i></div>

<h2 class="abs welcome-title">Welcome to Harvest Gateway Fellowship Ministries</h2>
<div class="abs welcome-text">
  <p>A place where we can come together and fellowship. HGFM is located in Riverside, Ohio and we would love to have you worship with us. We believe God is doing something extraordinary through our church and would like for you to be a part. Please prayerfully consider our church as a place you would like to worship and fellowship with us as we continue to grow.</p>
  <p>As you venture on our website please feel free to contact us through email, phone, or leave a prayer request for us to pray on your behalf. Please take a minute and look at our upcoming events.</p>
</div>
<div class="abs rule"></div>

<h2 class="abs staff-title">Our Staffs</h2>
<div class="abs card staff" style="left:74px"><div class="photo" role="img" aria-label="Portrait of the pastor in clerical collar"></div><div class="label">Pastor Daniel Okafor</div></div>
<div class="abs card staff" style="left:204px"><div class="photo" role="img" aria-label="Portrait of the minister"></div><div class="label">Minister Grace Okafor</div></div>

<h2 class="abs donate-title">Donations &amp; Products</h2>
<div class="abs card product gift" style="left:354px"><div class="photo" role="img" aria-label="Family holding a thank you sign"></div><div class="label">Donate Now</div></div>
<div class="abs card product books" style="left:484px"><div class="photo" role="img" aria-label="Open book with a wooden cross"></div><div class="label">Buy Now</div></div>

<section class="abs groups" role="img" aria-label="Large crowd gathered at a church event">
  <h3>Join our Group...</h3>
  <ul><li>Youth</li><li>Children's Church</li><li>Men</li><li class="more">and more..</li></ul>
</section>

<div class="abs video" role="img" aria-label="Video still of hands folded in prayer over a bible"></div>
<div class="abs play"><svg width="10" height="12" viewBox="0 0 10 12"><path d="M1 0l9 6-9 6z" fill="#333"/></svg></div>

<h2 class="abs events-title">Upcoming Events</h2>
<div class="abs cal">
  <div class="cal-head"><b>◄</b><span>June 2014</span><b>►</b></div>
  <div class="cal-days"><span>MON</span><span>TUE</span><span>WED</span><span>THU</span><span>FRI</span><span>SAT</span><span>SUN</span></div>
  <div class="cal-grid">
    <span class="off">28</span><span>1</span><span>2</span><span>3</span><span class="today">4</span><span>5</span><span>6</span>
    <span>7</span><span>8</span><span>9</span><span>10</span><span>11</span><span>12</span><span>13</span>
    <span>14</span><span>15</span><span>16</span><span>17</span><span>18</span><span>19</span><span>20</span>
    <span>21</span><span>22</span><span>23</span><span>24</span><span>25</span><span>26</span><span>27</span>
    <span>28</span><span>29</span><span>30</span><span>31</span><span class="off">1</span><span class="off">2</span><span class="off">3</span>
  </div>
</div>
<div class="abs event" style="top:846px"><h4>June 4th</h4><p>Nunc porttitor lacus lectus, sodales feugiat nisi laoreet eget.</p></div>
<div class="abs event" style="top:911px"><h4>June 4th</h4><p>Nunc porttitor lacus lectus, sodales feugiat nisi laoreet eget.</p></div>

<section class="abs verse">
  <h3>Random Bible Verse</h3>
  <p>For the wages of sin is death, but the gift of God is eternal life in Christ Jesus our Lord - <span>Romans 6:23</span></p>
</section>

<section class="abs contact">
  <div class="item" style="left:84px">
    <svg width="16" height="20" viewBox="0 0 16 20"><rect x="1" y="1" width="14" height="18" fill="#9a9a9a"/><rect x="4" y="4" width="2" height="12" fill="#ebebeb"/></svg>
    <span>214 Harvest Lane, Suite 3<br>Riverside, OH 45431</span>
  </div>
  <div class="item" style="left:287px;top:22px">
    <svg width="20" height="20" viewBox="0 0 20 20"><path d="M3 2l4 0 2 5-3 2c1 3 3 5 6 6l2-3 5 2 0 4c-8 1-17-8-16-16z" fill="#9a9a9a"/></svg>
    <span>Phone: 555.210.4830</span>
  </div>
  <div class="item" style="left:440px">
    <svg width="20" height="20" viewBox="0 0 20 20"><circle cx="10" cy="10" r="8.5" fill="none" stroke="#9a9a9a" stroke-width="1.5"/><path d="M10 5v5h4" stroke="#9a9a9a" stroke-width="1.5" fill="none"/></svg>
    <span>Mon-Fri &nbsp;9 A.M &nbsp;to &nbsp;8 P.M<br>Sat-Sun &nbsp;9 A.M &nbsp;to &nbsp;6 P.M</span>
  </div>
  <div class="item" style="left:620px;top:22px">
    <svg width="20" height="14" viewBox="0 0 20 14"><rect width="20" height="14" fill="#9a9a9a"/><path d="M0 0l10 8 10-8" stroke="#ebebeb" fill="none"/></svg>
    <span>E-mail : info@harvestgateway.org</span>
  </div>
</section>

<footer class="abs site-footer">
  <div class="copy">Copyright &nbsp;©&nbsp; 2014 &nbsp;Harvest Gateway Fellowship Ministries. &nbsp;All rights reserved.</div>
  <div class="cards" aria-label="Accepted payment methods"><span></span><span></span><span></span><span></span><span></span></div>
</footer>

</body>
</html>
```